Business Card Design Project - 2 sided

We need a business card design for a card having one business on each side (ie. two businesses on one card). Would like a design that incorporates logo, tagline and normal fields (name, position, address, phone).

Would also like an allowance for small font text along the bottom (text to be determined, but less than 50 characters).

NB. Attached logo for Harbor Quill has two variations - either can be used.

www.harborquill-example.com / www.velmaro-example.com

```html
<!DOCTYPE html>
<html lang="en">
<head>
<meta charset="utf-8">
<title>Harbor Quill / Velmaro business card</title>
<link href="https://fonts.googleapis.com/css2?family=Open+Sans:wght@400;600;700&display=swap" rel="stylesheet">
<style>
:root{
  --green:#8bc53f;
  --navy:#2a2a78;
  --grey:#6b6d70;
  --swoosh:#5f6062;
  --text:#4a4a4a;
  --card:#ffffff;
  --backdrop:#eceae6;
}
*{box-sizing:border-box;margin:0;padding:0}
html,body{width:1200px;height:487px;overflow:hidden}
body{background:var(--backdrop);font-family:"Open Sans",Arial,sans-serif;position:relative}
.card{position:absolute;top:88px;width:543px;height:311px;background:var(--card);border-radius:18px;overflow:hidden;box-shadow:0 2px 6px rgba(0,0,0,.18)}
.card--harbor{left:45px}
.card--velmaro{left:612px}
.card__header{position:absolute;inset:0 0 auto 0;width:543px;height:100px}
.card__person{position:absolute;top:22px;left:0;width:100%;text-align:center;color:#fff;font-size:17px;font-weight:700;letter-spacing:.2px}
.card__person span{font-weight:400;font-size:14px}
.brand{position:absolute;left:0;width:100%;text-align:center}
.brand__row{display:inline-flex;align-items:center;gap:10px}
.brand__dot{width:30px;height:30px;border-radius:50%;background:var(--green)}
.brand__name{font-size:30px;font-weight:600;color:var(--navy);letter-spacing:.5px}
.brand__tagline{font-size:10px;font-weight:700;color:var(--grey);margin-top:2px}
.card--harbor .brand{top:135px}
.card--velmaro .brand{top:130px}
.card--velmaro .brand__name{font-size:34px;color:#2f8fd0}
.card--velmaro .brand__tagline{font-size:13px;font-weight:400;letter-spacing:.6px;color:var(--text)}
.contacts{position:absolute;top:217px;left:44px;display:flex;font-size:13.5px;color:var(--text);line-height:20px}
.contacts__group{padding:0 10px;border-left:1px solid #9a9a9a}
.contacts__group:first-child{border-left:0;padding-left:0}
.contacts__item{display:flex;align-items:center;gap:6px}
.contacts__item svg{width:10px;height:10px;flex:none}
.card__footnote{position:absolute;top:262px;left:0;width:100%;text-align:center;font-size:10.5px;color:var(--text);letter-spacing:.3px}
</style>
</head>
<body>

<div class="card card--harbor">
  <svg class="card__header" viewBox="0 0 543 100" aria-hidden="true">
    <path fill="var(--green)" d="M0 0H543V42C480 60 420 78 340 80C220 82 120 38 0 46Z"/>
    <path fill="var(--swoosh)" d="M0 52C60 40 140 38 200 44C140 42 60 48 0 62Z"/>
    <path fill="var(--navy)" d="M300 80C400 84 480 66 543 42V50C480 74 400 88 300 80Z"/>
  </svg>
  <div class="card__person">YOUR NAME <span>/ Title</span></div>
  <div class="brand">
    <div class="brand__row"><span class="brand__dot"></span><span class="brand__name">HARBOR QUILL</span></div>
    <div class="brand__tagline">Website Translation and Localisation Specialist...</div>
  </div>
  <div class="contacts">
    <div class="contacts__group">
      <div class="contacts__item"><svg viewBox="0 0 10 10"><path fill="var(--green)" d="M2 0l2 2-1 2 3 3 2-1 2 2-2 2C4 10 0 6 0 2z"/></svg>123-456-7890</div>
      <div class="contacts__item"><svg viewBox="0 0 10 10"><rect x="2" y="0" width="6" height="10" rx="1" fill="var(--green)"/></svg>123-456-7890</div>
    </div>
    <div class="contacts__group">
      <div class="contacts__item"><svg viewBox="0 0 10 10"><rect y="2" width="10" height="7" fill="var(--green)"/></svg>name@website.com</div>
      <div class="contacts__item"><svg viewBox="0 0 10 10"><circle cx="5" cy="5" r="5" fill="var(--green)"/></svg>www.website.com</div>
    </div>
    <div class="contacts__group">
      <div>Complex name, Street</div>
      <div>City, State, zip code</div>
    </div>
  </div>
  <div class="card__footnote">xxxxxxxxxxxxxxxxxxxxxxxxxxxxxxxxxxxxxxxxxxxxxxxx</div>
</div>

<div class="card card--velmaro">
  <svg class="card__header" viewBox="0 0 543 100" aria-hidden="true">
    <path fill="var(--green)" d="M0 0H543V42C480 60 420 78 340 80C220 82 120 38 0 46Z"/>
    <path fill="var(--swoosh)" d="M0 52C60 40 140 38 200 44C140 42 60 48 0 62Z"/>
    <path fill="var(--navy)" d="M300 80C400 84 480 66 543 42V50C480 74 400 88 300 80Z"/>
  </svg>
  <div class="card__person">YOUR NAME <span>/ Title</span></div>
  <div class="brand">
    <div class="brand__row"><span class="brand__dot"></span><span class="brand__name">velmaro</span></div>
    <div class="brand__tagline">Professional SEO Services</div>
  </div>
  <div class="contacts">
    <div class="contacts__group">
      <div class="contacts__item"><svg viewBox="0 0 10 10"><path fill="var(--green)" d="M2 0l2 2-1 2 3 3 2-1 2 2-2 2C4 10 0 6 0 2z"/></svg>123-456-7890</div>
      <div class="contacts__item"><svg viewBox="0 0 10 10"><rect x="2" y="0" width="6" height="10" rx="1" fill="var(--green)"/></svg>123-456-7890</div>
    </div>
    <div class="contacts__group">
      <div class="contacts__item"><svg viewBox="0 0 10 10"><rect y="2" width="10" height="7" fill="var(--green)"/></svg>name@website.com</div>
      <div class="contacts__item"><svg viewBox="0 0 10 10"><circle cx="5" cy="5" r="5" fill="var(--green)"/></svg>www.website.com</div>
    </div>
    <div class="contacts__group">
      <div>Complex name, Street</div>
      <div>City, State, zip code</div>
    </div>
  </div>
  <div class="card__footnote">xxxxxxxxxxxxxxxxxxxxxxxxxxxxxxxxxxxxxxxxxxxxxxxx</div>
</div>

</body>
</html>
```